TALMORK

The business want a professional looking business card. We have a scetch we will add but want the extra upgrade, and would like more suggestions for variations of our business cards.

```html
<!DOCTYPE html>
<html lang="en">
<head>
<meta charset="utf-8">
<title>TALMORK – Business Card</title>
<link rel="stylesheet" href="https://fonts.googleapis.com/css2?family=Montserrat:wght@400;500;600;700&family=Nunito+Sans:wght@400;600&display=swap">
<style>
  :root {
    --backdrop: #5f4b41;
    --paper: #f4f1ea;
    --gold: #c69a2a;
    --gold-light: #e9c15f;
    --gold-deep: #b48a22;
    --ink: #1d1d1d;
    --white: #ffffff;
  }
  * { box-sizing: border-box; margin: 0; padding: 0; }
  html, body { width: 1200px; height: 800px; overflow: hidden; }
  body {
    background: var(--backdrop);
    font-family: "Nunito Sans", sans-serif;
    display: flex;
    flex-direction: column;
    align-items: center;
    justify-content: center;
    gap: 40px;
  }
  .card {
    position: relative;
    width: 600px;
    height: 343px;
    border-radius: 22px;
    overflow: hidden;
  }
  .card-front { background: var(--paper); }
  .front-swoosh { position: absolute; inset: 0; }

  .brand-lockup {
    position: absolute;
    left: 120px;
    top: 140px;
    width: 180px;
    text-align: center;
  }
  .brand-name {
    font-family: "Montserrat", sans-serif;
    font-weight: 700;
    font-size: 30px;
    letter-spacing: 2px;
    color: var(--gold-deep);
    line-height: 1;
  }
  .brand-since {
    display: flex;
    align-items: center;
    justify-content: center;
    gap: 8px;
    margin-top: 6px;
    font-family: "Montserrat", sans-serif;
    font-weight: 500;
    font-size: 11px;
    letter-spacing: 2px;
    color: #3b3b3b;
  }
  .brand-since::before, .brand-since::after {
    content: "";
    width: 30px;
    height: 1px;
    background: var(--gold);
  }

  .holder {
    position: absolute;
    left: 322px;
    top: 62px;
  }
  .holder-company {
    font-family: "Montserrat", sans-serif;
    font-weight: 700;
    font-size: 14px;
    color: var(--gold-deep);
    letter-spacing: 0.3px;
  }
  .holder-role, .holder-name {
    font-size: 14px;
    color: var(--ink);
    line-height: 1.35;
  }
  .holder-role { margin-top: 4px; }

  .divider {
    position: absolute;
    left: 326px;
    top: 142px;
    width: 256px;
    height: 1.5px;
    background: var(--gold);
  }
  .divider::before {
    content: "";
    position: absolute;
    left: -3px;
    top: -3px;
    width: 7px;
    height: 7px;
    border-radius: 50%;
    background: var(--gold);
  }

  .contact-rail {
    position: absolute;
    left: 318px;
    top: 208px;
    width: 20px;
    height: 150px;
    border-radius: 10px 10px 0 0;
    background: var(--gold);
  }
  .contact-list {
    position: absolute;
    left: 318px;
    top: 213px;
    list-style: none;
  }
  .contact-item {
    display: flex;
    align-items: center;
    gap: 12px;
    height: 25px;
    font-size: 13px;
    color: var(--ink);
  }
  .contact-icon { width: 20px; height: 14px; flex: none; }

  .card-back {
    background: linear-gradient(135deg, var(--gold-deep) 0%, var(--gold) 45%, var(--gold-light) 100%);
    display: flex;
    align-items: center;
    justify-content: center;
  }
  .card-back .brand-name { color: var(--white); font-size: 40px; letter-spacing: 3px; }
  .card-back .brand-since { color: var(--white); font-size: 13px; margin-top: 8px; }
  .card-back .brand-since::before, .card-back .brand-since::after { background: var(--white); width: 60px; }
  .back-lockup { text-align: center; }
</style>
</head>
<body>
  <section class="card card-front" aria-label="Business card front">
    <svg class="front-swoosh" viewBox="0 0 600 343" aria-hidden="true">
      <path d="M0,0 H70 C40,70 50,140 70,190 C95,260 150,315 215,343 H0 Z" fill="var(--gold)"/>
      <path d="M62,0 C38,70 46,150 66,200 C92,265 150,318 212,343" fill="none" stroke="var(--paper)" stroke-width="9"/>
      <path d="M72,0 H112 C88,40 78,100 76,170 C66,110 62,50 72,0 Z" fill="var(--ink)"/>
      <path d="M80,190 C90,250 140,310 215,343 H240 C160,315 105,260 80,190 Z" fill="var(--gold)"/>
    </svg>

    <div class="brand-lockup">
      <p class="brand-name">TALMORK</p>
      <p class="brand-since">SINCE 2026</p>
    </div>

    <div class="holder">
      <p class="holder-company">TALMORK BRENVIK</p>
      <p class="holder-role">CEO &amp; Founder</p>
      <p class="holder-name">Mats Olav Brenvik</p>
    </div>
    <div class="divider"></div>

    <div class="contact-rail"></div>
    <ul class="contact-list">
      <li class="contact-item">
        <svg class="contact-icon" viewBox="0 0 20 14" aria-hidden="true"><path d="M7 2 C6 4 7 9 12 12 L14 10 L12 8 L11 9 C9.5 8 8.5 6.5 8.5 5 L9.5 4 Z" fill="var(--white)"/></svg>
        004795550142
      </li>
      <li class="contact-item">
        <svg class="contact-icon" viewBox="0 0 20 14" aria-hidden="true"><rect x="4" y="3" width="12" height="8" fill="none" stroke="var(--white)" stroke-width="1.2"/><path d="M4 3 L10 8 L16 3" fill="none" stroke="var(--white)" stroke-width="1.2"/></svg>
        talmork.llc@mailbox.com
      </li>
      <li class="contact-item">
        <svg class="contact-icon" viewBox="0 0 20 14" aria-hidden="true"><g fill="none" stroke="var(--white)" stroke-width="1"><circle cx="10" cy="7" r="5.5"/><ellipse cx="10" cy="7" rx="2.4" ry="5.5"/><path d="M4.5 7 H15.5 M5.5 4.2 H14.5 M5.5 9.8 H14.5"/></g></svg>
        www.talmork.llc
      </li>
    </ul>
  </section>

  <section class="card card-back" aria-label="Business card back">
    <div class="back-lockup">
      <p class="brand-name">TALMORK</p>
      <p class="brand-since">SINCE 2026</p>
    </div>
  </section>
</body>
</html>
```